Copper Lantern

Need a business card for our restaurant. Restaurant and Bar in the mountains of North Idaho. Rustic looking card

rustic design, wood and metal looking, primarily neutral colors

• Name, address, phone number, website, email address

```html
<!DOCTYPE html>
<html lang="en">
<head>
<meta charset="utf-8">
<title>Copper Lantern – Business Card</title>
<link rel="stylesheet" href="https://fonts.googleapis.com/css2?family=Archivo+Narrow:wght@700&family=Archivo:wght@700&family=Cinzel:wght@400;500&family=Roboto+Slab:wght@400;800&display=swap">
<style>
  :root {
    --bg-top: #ffffff;
    --bg-bottom: #b3a698;
    --title-dark: #9a8a7b;
    --title-light: #cfc4b8;
    --wood-dark-1: #2a2a2a;
    --wood-dark-2: #3e3e3e;
    --wood-dark-3: #1c1c1c;
    --gold: #c9a457;
    --gold-light: #e6c987;
    --wood-light-1: #d9a94f;
    --wood-light-2: #e8c274;
    --wood-light-3: #c48f3a;
    --ink: #4a2e10;
    --illus: #3f2508;
    --label: #ffffff;
  }
  * { margin: 0; padding: 0; box-sizing: border-box; }
  html, body { width: 675px; height: 1200px; overflow: hidden; }
  body {
    background: linear-gradient(180deg, var(--bg-top) 0%, var(--bg-top) 22%, var(--bg-bottom) 100%);
    position: relative;
    font-family: "Roboto Slab", serif;
  }
  .board-title {
    position: absolute; left: 54px; top: 150px;
    font-family: "Archivo Narrow", sans-serif; font-weight: 700;
    font-size: 34px; line-height: 29px; letter-spacing: -1px;
  }
  .board-title .line-one { color: var(--title-dark); display: block; }
  .board-title .line-two { color: var(--title-light); display: block; }

  .card {
    position: absolute; left: 57px; width: 561px; height: 320px;
    box-shadow: 0 10px 24px rgba(0,0,0,0.28);
    overflow: hidden;
  }
  .card-back { top: 260px;
    background:
      repeating-linear-gradient(172deg, rgba(255,255,255,0.03) 0 3px, rgba(0,0,0,0.05) 3px 7px),
      linear-gradient(135deg, var(--wood-dark-2), var(--wood-dark-1) 45%, var(--wood-dark-3));
  }
  .card-front { top: 680px;
    background:
      repeating-linear-gradient(178deg, rgba(120,70,10,0.06) 0 2px, rgba(255,230,170,0.05) 2px 6px),
      linear-gradient(120deg, var(--wood-light-2), var(--wood-light-1) 50%, var(--wood-light-3));
  }

  .emblem {
    position: absolute; left: 50%; top: 50%; transform: translate(-50%, -50%);
    display: flex; align-items: center; gap: 12px;
  }
  .emblem-dot { width: 18px; height: 18px; border-radius: 50%; background: var(--gold); }
  .emblem-name {
    font-family: "Cinzel", serif; font-weight: 500; font-size: 30px;
    letter-spacing: 3px; color: var(--gold-light);
  }

  .brand { position: absolute; left: 30px; top: 42px; color: var(--ink); }
  .brand-name { font-family: "Cinzel", serif; font-size: 20px; letter-spacing: 1px; }
  .brand-sub { font-family: "Cinzel", serif; font-size: 8px; letter-spacing: 7px; margin-top: 1px; }

  .illustration {
    position: absolute; right: 52px; top: 0; width: 160px; height: 200px;
    background: linear-gradient(180deg, rgba(63,37,8,0.55), rgba(63,37,8,0.85));
    border-radius: 0 0 60px 60px;
  }

  .person { position: absolute; left: 30px; top: 150px; color: var(--ink); }
  .person-name { font-weight: 800; font-size: 27px; letter-spacing: 0.5px; line-height: 1; }
  .person-role { font-family: "Cinzel", serif; font-size: 12px; margin-top: 2px; }

  .contact { position: absolute; left: 30px; top: 232px; list-style: none; color: var(--ink); }
  .contact li { display: flex; align-items: center; gap: 8px; font-size: 12px; line-height: 15px; }
  .contact svg { width: 11px; height: 11px; fill: var(--ink); flex: none; }

  .card-label {
    position: absolute; width: 675px; text-align: center;
    font-family: "Archivo", sans-serif; font-weight: 700; font-size: 12px;
    letter-spacing: 1.5px; color: var(--label);
  }
  .label-back { top: 594px; }
  .label-front { top: 1014px; }
</style>
</head>
<body>
  <h1 class="board-title"><span class="line-one">BUSINESS CARD</span><span class="line-two">DESIGN</span></h1>

  <section class="card card-back">
    <div class="emblem">
      <span class="emblem-dot"></span>
      <span class="emblem-name">Copper Lantern</span>
    </div>
  </section>
  <p class="card-label label-back">BACK SIDE DESIGN</p>

  <section class="card card-front">
    <div class="brand">
      <div class="brand-name">THE COPPER LANTERN</div>
      <div class="brand-sub">RESTAURANT &amp; BAR</div>
    </div>
    <div class="illustration" role="img" aria-label="Dark brown illustration of the restaurant's mascot animal hanging upside down"></div>
    <div class="person">
      <div class="person-name">JOHN DOE</div>
      <div class="person-role">GENERAL MANAGER</div>
    </div>
    <ul class="contact">
      <li><svg viewBox="0 0 12 12"><path d="M6 0a4 4 0 0 0-4 4c0 3 4 8 4 8s4-5 4-8a4 4 0 0 0-4-4zm0 5.5A1.5 1.5 0 1 1 6 2.5a1.5 1.5 0 0 1 0 3z"/></svg>218 Cedar St, Mullan, ID 83846</li>
      <li><svg viewBox="0 0 12 12"><path d="M2.5 0.5l2 2.5-1.2 1.4a7 7 0 0 0 4.3 4.3L9 7.5l2.5 2-1 2C5 11.5 0.5 7 0.5 1.5z"/></svg>(208) 555-0147</li>
      <li><svg viewBox="0 0 12 12"><path d="M0 2h12v8H0zM1 3v.3l5 3.2 5-3.2V3z"/></svg>hello@copperlanternidaho.com</li>
      <li><svg viewBox="0 0 12 12"><path d="M6 0a6 6 0 1 0 0 12A6 6 0 0 0 6 0zm0 1.2c.6.6 1.2 2 1.3 4.2H4.7C4.8 3.2 5.4 1.8 6 1.2zM1.3 6.6h2.3c.1 1.6.4 2.9.9 3.8a4.8 4.8 0 0 1-3.2-3.8zm0-1.2a4.8 4.8 0 0 1 3.2-3.8c-.5.9-.8 2.2-.9 3.8zm4.7 5.4c-.6-.6-1.2-2-1.3-4.2h2.6c-.1 2.2-.7 3.6-1.3 4.2zm1.5-.4c.5-.9.8-2.2.9-3.8h2.3a4.8 4.8 0 0 1-3.2 3.8zm.9-5c-.1-1.6-.4-2.9-.9-3.8a4.8 4.8 0 0 1 3.2 3.8z"/></svg>copperlanternidaho.com</li>
    </ul>
  </section>
  <p class="card-label label-front">FRONT SIDE DESIGN</p>
</body>
</html>
```